Ward Compass Business Card Design*

We need a business card design for our company Ward Compass. Our company is specialized in providing online consulting services regarding medical institutions, hospitals and doctors. We work with patients worldwide looking to choose between healthcare providers. We have a website you may use as a reference, where we list doctors and clinics worldwide. So we target Medical providers as well as patients worldwide.
Target Market(s)
Medical Providers and patients around the world
Industry/Entity Type
Medical
Contact Information for Business Card
Salwa Kettani
CEO
+90 612 348 2175
info@wardcompass.example
www.wardcompass.example
14 Annakhil 7 H.R.B. Rabat, Morocco
Requirements
Must have
- Company logo/name on one full side, personal info and smaller logo and company name on the other side.
Nice to have
- Smart and elegant design

```html
<!DOCTYPE html>
<html lang="en">
<head>
<meta charset="utf-8">
<title>Ward Compass Business Card</title>
<link rel="stylesheet" href="https://fonts.googleapis.com/css2?family=Poppins:wght@300;400;600&display=swap">
<style>
  :root {
    --navy: #173f6e;
    --navy-dark: #12335b;
    --grey: #8a8a8a;
    --white: #ffffff;
    --ink: #1f2d44;
    --stage: #2b2b2b;
  }
  * { margin: 0; padding: 0; box-sizing: border-box; }
  html, body {
    width: 1200px; height: 960px; overflow: hidden;
    background: var(--stage);
    font-family: "Poppins", sans-serif;
  }
  .stage {
    width: 1200px; height: 960px;
    display: flex; flex-direction: column; align-items: center; justify-content: center;
    gap: 50px;
  }
  .card {
    position: relative;
    width: 700px; height: 400px;
    overflow: hidden;
    box-shadow: 0 10px 30px rgba(0,0,0,.45);
  }
  /* Front side */
  .card-front {
    background: var(--navy);
    display: flex; align-items: center; justify-content: center;
  }
  .brand {
    display: flex; align-items: center; gap: 16px;
    color: var(--white);
    font-weight: 400;
    font-size: 34px;
    letter-spacing: 2px;
    text-transform: uppercase;
  }
  .brand-dot {
    width: 46px; height: 46px; border-radius: 50%;
    border: 6px solid currentColor;
  }
  /* Back side */
  .card-back { background: var(--navy); }
  .card-back .swoosh { position: absolute; inset: 0; }
  .back-brand {
    position: absolute; top: 44px; right: 46px;
    display: flex; flex-direction: column; align-items: flex-end;
  }
  .back-brand .brand {
    color: var(--navy); font-size: 24px; gap: 12px; letter-spacing: 1.5px;
  }
  .back-brand .brand-dot { width: 34px; height: 34px; border-width: 5px; }
  .person-name {
    margin-top: 8px;
    color: var(--navy); font-weight: 600; font-size: 26px;
  }
  .person-role {
    color: var(--grey); font-size: 13px; letter-spacing: 1px;
  }
  .contact {
    position: absolute; left: 46px; bottom: 34px;
    color: var(--ink); font-size: 14px; line-height: 1.45;
  }
  .address { margin-bottom: 10px; }
  .contact-line { display: flex; align-items: center; gap: 10px; }
  .contact-line svg { width: 13px; height: 13px; fill: var(--navy); flex: none; }
</style>
</head>
<body>
<main class="stage">
  <section class="card card-front" aria-label="Card front">
    <div class="brand"><span class="brand-dot"></span>Ward Compass</div>
  </section>

  <section class="card card-back" aria-label="Card back">
    <svg class="swoosh" viewBox="0 0 700 400" aria-hidden="true">
      <ellipse cx="350" cy="205" rx="440" ry="205" transform="rotate(-24 350 205)" fill="#8a8a8a"/>
      <ellipse cx="362" cy="198" rx="432" ry="198" transform="rotate(-24 362 198)" fill="#ffffff"/>
    </svg>

    <div class="back-brand">
      <div class="brand"><span class="brand-dot"></span>Ward Compass</div>
      <div class="person-name">Salwa Kettani</div>
      <div class="person-role">CEO</div>
    </div>

    <div class="contact">
      <p class="address">14 Annakhil 7 H.R.B.<br>Rabat, Morocco</p>
      <p class="contact-line">
        <svg viewBox="0 0 24 24"><path d="M6.6 10.8a15.1 15.1 0 0 0 6.6 6.6l2.2-2.2a1 1 0 0 1 1-.25 11.4 11.4 0 0 0 3.6.57 1 1 0 0 1 1 1V20a1 1 0 0 1-1 1A17 17 0 0 1 3 4a1 1 0 0 1 1-1h3.5a1 1 0 0 1 1 1c0 1.25.2 2.45.57 3.57a1 1 0 0 1-.25 1z"/></svg>
        +90 612 348 2175
      </p>
      <p class="contact-line">
        <svg viewBox="0 0 24 24"><path d="M2 5h20v14H2zm2 2v.5l8 5 8-5V7l-8 5z"/></svg>
        info@wardcompass.example
      </p>
      <p class="contact-line">
        <svg viewBox="0 0 24 24"><circle cx="12" cy="12" r="10"/></svg>
        www.wardcompass.example
      </p>
    </div>
  </section>
</main>
</body>
</html>
```